We are Here! Come and Meet the Team Flyer

A clear and quirky, flyer to let local Residents know we have landed.
Based around our logo.

We avoid anything medical but rather focus on being pet-centred, warmth, approachable and community-orientated.

We pride ourselves on being cutting-edge but steer away from a cold sterile image.
Approachability, uptodate. We understandt hat pets are part of a family and we will provide the level of care that we would expect for our own pets.

Target Market(s)

Residents in the area

Industry/Entity Type

Veterinary

Font styles to use
Sans Serif

Colors
33b8a4
ffc214
0255a3

Requirements
Must have
• Logo and PERHAPS a location of Clinic indicated on the cat of the Logo.
• NOW OPEN!
• 1) Exact location of the Clinic indicated: the lefthand side of tail, near the cat's back.
• 2) Warm, quirky, Approachable
• 3) Contact details (see attached draft Poster)
• 4) Location: Silver Brook Arcade, Building 4, Mezzanine level
Should not have
• nothing medical or cliched.

```html
<!DOCTYPE html>
<html lang="en">
<head>
<meta charset="utf-8">
<title>Tails &amp; Toes Veterinary Clinic – Flyer</title>
<link href="https://fonts.googleapis.com/css2?family=Open+Sans:wght@300;400;700&display=swap" rel="stylesheet">
<style>
  :root {
    --backdrop: #6e6a68;
    --paper: #ffffff;
    --blue: #0c55a5;
    --sage: #8bbba0;
    --orange: #d98a2e;
    --teal-ink: #3f7f8c;
    --photo-warm: #d9b48a;
    --photo-cool: #cfdde6;
  }
  * { margin: 0; padding: 0; box-sizing: border-box; }
  html, body { width: 923px; height: 1200px; overflow: hidden; }
  body {
    background: var(--backdrop);
    font-family: "Open Sans", Arial, sans-serif;
    position: relative;
  }
  .flyer {
    position: absolute;
    left: 80px; top: 60px;
    width: 763px; height: 1080px;
    background: var(--paper);
    overflow: hidden;
  }
  .shapes { position: absolute; inset: 0; }
  .headline {
    position: absolute;
    left: 210px; top: 48px; width: 420px;
    color: var(--paper);
    text-align: center;
  }
  .headline .kicker {
    font-weight: 300; font-size: 40px; letter-spacing: 0.5px; line-height: 1.1;
    text-align: left; padding-left: 28px;
  }
  .headline .lead {
    font-weight: 700; font-size: 29px; line-height: 38px; margin-top: 8px;
  }
  .photo {
    position: absolute;
    left: -13px; top: 247px;
    width: 380px; height: 380px;
    border-radius: 50%;
    border: 8px solid var(--paper);
    box-shadow: 0 2px 6px rgba(0,0,0,0.25);
    background: radial-gradient(circle at 55% 45%, var(--photo-warm) 0%, #c79a63 40%, var(--photo-cool) 80%);
  }
  .contact-bars { position: absolute; left: 460px; top: 428px; width: 303px; }
  .bar {
    height: 37px; margin-bottom: 8px;
    display: flex; align-items: center;
    color: var(--paper); font-weight: 700; font-size: 17px;
  }
  .bar svg { width: 22px; height: 22px; margin: 0 18px 0 16px; }
  .bar--phone { background: var(--orange); }
  .bar--mobile { background: var(--sage); }
  .bar--web { background: var(--blue); }
  .brand {
    position: absolute; left: 160px; top: 745px;
    display: flex; align-items: center; gap: 14px;
  }
  .brand-dot { width: 34px; height: 34px; border-radius: 50%; background: var(--sage); }
  .brand-name { font-size: 38px; font-weight: 700; color: var(--teal-ink); letter-spacing: -0.5px; }
  .contact-tag {
    position: absolute; left: 485px; top: 692px;
    width: 278px; height: 38px;
    background: var(--blue);
    clip-path: polygon(0 0, 100% 0, 100% 100%, 9% 100%);
    box-shadow: 0 4px 6px rgba(0,0,0,0.3);
    color: var(--paper); font-weight: 700; font-size: 21px;
    display: flex; align-items: center; padding-left: 62px;
  }
  .address {
    position: absolute; left: 498px; top: 756px;
    display: flex; gap: 14px;
    color: var(--blue); font-size: 17px; line-height: 23px;
  }
  .address svg { width: 22px; height: 36px; margin-top: 4px; flex: none; }
  .open-badge {
    position: absolute; left: 522px; top: 870px;
    width: 226px; height: 226px; border-radius: 50%;
    background: var(--orange);
    border: 8px solid var(--paper);
    box-shadow: 0 2px 6px rgba(0,0,0,0.3);
    color: var(--paper); font-weight: 700; font-size: 28px; line-height: 37px;
    text-align: center;
    display: flex; align-items: center; justify-content: center;
    padding-bottom: 18px;
  }
  .social {
    position: absolute; left: 88px; top: 1000px;
    display: grid; grid-template-columns: 216px 200px; row-gap: 9px;
    color: var(--paper); font-size: 15px;
  }
  .social span { display: flex; align-items: center; gap: 10px; }
  .social .dot { width: 12px; height: 12px; border-radius: 50%; background: var(--paper); }
  .social svg { width: 16px; height: 12px; }
</style>
</head>
<body>
  <main class="flyer">
    <svg class="shapes" width="763" height="1080" viewBox="0 0 763 1080">
      <polygon points="0,140 0,185 530,330 763,8 763,0 750,0" fill="var(--sage)"/>
      <polygon points="0,0 755,0 520,282 0,145" fill="var(--blue)"/>
      <polygon points="0,1010 135,870 763,950 763,972 125,915 0,1032" fill="var(--sage)"/>
      <polygon points="0,1080 0,1030 125,915 763,970 763,1080" fill="var(--blue)"/>
    </svg>

    <header class="headline">
      <p class="kicker">DID YOU KNOW?</p>
      <p class="lead">The Crescent Isle now has its own Veterinary Clinic</p>
    </header>

    <div class="photo" role="img" aria-label="Photo of a smiling woman with a golden retriever and an orange and white cat"></div>

    <section class="contact-bars">
      <div class="bar bar--phone">
        <svg viewBox="0 0 24 24"><path d="M3 9c0-3 4-5 9-5s9 2 9 5l-1 2-4-1V8c-2-1-6-1-8 0v2l-4 1zM6 13h12l2 7H4z" fill="#fff"/><circle cx="12" cy="16" r="2" fill="var(--orange)"/></svg>
        800-7TT-VETS
      </div>
      <div class="bar bar--mobile">
        <svg viewBox="0 0 24 24"><rect x="7" y="2" width="10" height="20" rx="2" fill="#fff"/><rect x="9" y="5" width="6" height="8" fill="var(--sage)"/></svg>
        04 5550192
      </div>
      <div class="bar bar--web">
        <svg viewBox="0 0 24 24" fill="none" stroke="#fff" stroke-width="1.8"><circle cx="12" cy="12" r="9"/><ellipse cx="12" cy="12" rx="4" ry="9"/><path d="M3 12h18M5 7h14M5 17h14"/></svg>
        www.tailstoesvet.ae
      </div>
    </section>

    <div class="brand">
      <span class="brand-dot"></span>
      <span class="brand-name">tails &amp; toes</span>
    </div>

    <div class="contact-tag">CONTACT US:</div>

    <address class="address" style="font-style:normal">
      <svg viewBox="0 0 22 36"><path d="M11 1a9 9 0 0 0-9 9c0 7 9 16 9 16s9-9 9-16a9 9 0 0 0-9-9z" fill="var(--orange)"/><circle cx="11" cy="10" r="3.5" fill="#fff"/><ellipse cx="11" cy="33" rx="7" ry="2" fill="#333"/></svg>
      <span>Mezzanine Level,<br>Building 4,<br>Silver Brook Arcade 1<br>(Above Cafe Lumo)</span>
    </address>

    <div class="open-badge">OPEN<br>7 DAYS<br>A WEEK</div>

    <footer class="social">
      <span><i class="dot"></i>@TailsToesVets</span>
      <span><i class="dot"></i>@tailstoesclinic</span>
      <span><i class="dot"></i>@tailstoesvet</span>
      <span><svg viewBox="0 0 16 12"><rect x="0.8" y="0.8" width="14.4" height="10.4" fill="none" stroke="#fff" stroke-width="1.6"/><path d="M1 1l7 6 7-6" fill="none" stroke="#fff" stroke-width="1.6"/></svg>hello@tailstoesvet.ae</span>
    </footer>
  </main>
</body>
</html>
```